We are a new company with 2 divisions a medical research and medical product sales. We need a company logo and Business Cards. The design files need to be provided to us in Adobe Photoshop CS 5.1.

Target Market(s)

Medical Community

Industry/Entity Type

Medical

Contact Information for Business Card

Company Name - Harrowgate Lifesciences LLC
Company Address 4127 Larkspur Ave Suite 7, Gainesville Fl 32614

Requirements
Must have
• The design files need to be provided to us in Adobe Photoshop CS 5.1.

```html
<!DOCTYPE html>
<html lang="en">
<head>
<meta charset="utf-8">
<title>Harrowgate Lifesciences LLC – Business Card</title>
<link href="https://fonts.googleapis.com/css2?family=Lato:wght@400;700&display=swap" rel="stylesheet">
<style>
  :root {
    --backdrop: #2e2e2e;
    --card: #ffffff;
    --accent: #d9472b;
    --ink: #3a3a3a;
    --muted: #5a5a5a;
    --rule: #cfcfcf;
  }
  * { box-sizing: border-box; margin: 0; padding: 0; }
  html, body {
    width: 1200px;
    height: 900px;
    overflow: hidden;
    background: var(--backdrop);
    font-family: "Lato", sans-serif;
  }
  .business-card {
    position: absolute;
    left: 180px;
    top: 210px;
    width: 840px;
    height: 479px;
    background: var(--card);
    border-radius: 24px;
    overflow: hidden;
  }
  .brand {
    position: absolute;
    left: 556px;
    top: 62px;
    width: 200px;
    text-align: center;
  }
  .brand-dot {
    display: block;
    width: 34px;
    height: 34px;
    margin: 0 auto 18px;
    border-radius: 50%;
    background: var(--accent);
  }
  .brand-name {
    color: var(--accent);
    font-weight: 700;
    font-size: 22px;
    line-height: 1.2;
    text-transform: uppercase;
    letter-spacing: 0.5px;
  }
  .holder {
    position: absolute;
    left: 74px;
    top: 254px;
  }
  .holder-name {
    color: var(--ink);
    font-weight: 700;
    font-size: 25px;
    line-height: 1.2;
  }
  .holder-title {
    color: var(--accent);
    font-size: 19px;
    line-height: 1.3;
  }
  .divider {
    position: absolute;
    left: 332px;
    top: 274px;
    width: 410px;
    height: 1px;
    background: var(--rule);
  }
  .address {
    position: absolute;
    right: 108px;
    top: 300px;
    text-align: right;
    color: var(--muted);
    font-size: 20px;
    line-height: 1.5;
  }
  .contact {
    position: absolute;
    right: 80px;
    top: 362px;
    text-align: right;
    color: var(--muted);
    font-size: 17px;
  }
  .contact-line {
    display: flex;
    align-items: center;
    justify-content: flex-end;
    gap: 10px;
    height: 30px;
  }
  .contact-icon { width: 18px; height: 16px; fill: var(--accent); }
  .band {
    position: absolute;
    left: 0;
    top: 0;
    width: 840px;
    height: 479px;
  }
  .band path { fill: var(--accent); }
  .website {
    position: absolute;
    left: 74px;
    top: 416px;
    color: #ffffff;
    font-size: 18px;
  }
</style>
</head>
<body>
  <div class="business-card">
    <svg class="band" viewBox="0 0 840 479" aria-hidden="true">
      <path d="M0 394 L368 394 C392 394 400 404 406 420 C413 440 422 450 448 450 L840 450 L840 479 L0 479 Z"/>
    </svg>

    <div class="brand">
      <span class="brand-dot"></span>
      <div class="brand-name">Harrowgate<br>Lifesciences LLC</div>
    </div>

    <div class="holder">
      <div class="holder-name">Name of the Person</div>
      <div class="holder-title">Managing Director</div>
    </div>
    <div class="divider"></div>

    <div class="address">
      4127 Larkspur Ave Suite 7,<br>Gainesville Fl 32614
    </div>

    <div class="contact">
      <div class="contact-line">
        <span>044 2718 40963</span>
        <svg class="contact-icon" viewBox="0 0 18 16" aria-label="Phone">
          <path d="M2 4 C2 1.5 5 0.5 9 0.5 C13 0.5 16 1.5 16 4 L16 6 L12.5 6 L12.5 4 L5.5 4 L5.5 6 L2 6 Z"/>
          <path d="M4 8 L6 6 L12 6 L14 8 L15 15 L3 15 Z"/>
        </svg>
      </div>
      <div class="contact-line">
        <span>info@harrowgatelifesciences.com</span>
        <svg class="contact-icon" viewBox="0 0 18 16" aria-label="Email">
          <path d="M1 3 L17 3 L17 14 L1 14 Z M2.5 4.5 L9 9.5 L15.5 4.5 Z" fill-rule="evenodd"/>
        </svg>
      </div>
    </div>

    <div class="website">www.harrowgatelifesciences.com</div>
  </div>
</body>
</html>
```